Wren Hollow Farm Postcard Design

I am looking for a new postcard design to mail out this season. We are a Farm business that does wholesale and retail and bulk seasoned firewood sales. we sell firewood from anything from bagged wood to tractor trailer loads of wood. We sell firewood in bulk bags. Pick up or delivery available there is no order to big or too small. I need my business name and phone number on the cards Wren Hollow Farm 615-302-4187 (call or text) I would like it to say we are the best priced guaranteed. I want something that is simple and straight forward but also really catches the eye when they see these in the mail box. I attached my logo and feel free to use photos of split firewood if you would like. id like my email on the card Wrenhollowfarm47@maplepost.net.

Target Market(s)

Firewood purchasers

Industry/Entity Type

agriculture

Requirements
Must have
• email phone number logo

```html
<!DOCTYPE html>
<html lang="en">
<head>
<meta charset="utf-8">
<title>Wren Hollow Farm – Firewood Postcard</title>
<link href="https://fonts.googleapis.com/css2?family=Sora:wght@400;600;700;800&display=swap" rel="stylesheet">
<style>
  :root{
    --backdrop:#5f77ae;
    --ink:#0a0a0a;
    --red:#dc3545;
    --white:#ffffff;
    --gold:#e6c25a;
    --amber:#f6b421;
    --orange:#ee7d1e;
    --yellow:#f7d40c;
    --rule:#555555;
  }
  *{box-sizing:border-box;margin:0;padding:0}
  html,body{width:876px;height:1200px;overflow:hidden}
  body{background:var(--backdrop);font-family:'Sora',sans-serif;position:relative}
  .postcard{position:absolute;left:83px;width:709px;height:473px;overflow:hidden;background:var(--white)}
  .postcard--front{top:89px}
  .postcard--back{top:622px}
  .postcard__art{position:absolute;inset:0;width:709px;height:473px}
  .brand{position:absolute;left:12px;top:17px;width:212px;height:73px;background:#111;display:flex;align-items:center;justify-content:center;gap:8px}
  .brand__mark{width:12px;height:12px;border-radius:50%;background:var(--gold)}
  .brand__name{color:var(--gold);font-weight:800;font-size:19px;line-height:1.05;letter-spacing:.5px;text-transform:uppercase}
  .firm-title{position:absolute;left:21px;color:var(--white);font-weight:700;font-size:26px;letter-spacing:.3px}
  .firm-note{position:absolute;left:21px;color:var(--gold);font-size:18.5px;line-height:24px}
  .front-note{top:137px;font-weight:700}
  .back-note{top:148px;font-weight:400;left:25px}
  .headline{position:absolute;left:318px;top:22px;color:var(--ink);font-weight:700;font-size:23.5px;line-height:27px;text-align:center}
  .sales{position:absolute;left:497px;top:14px;color:var(--white);font-weight:800;font-size:53px;letter-spacing:1px}
  .channels{position:absolute;left:318px;top:96px;height:31px;line-height:31px;color:var(--white);font-weight:700;font-size:23.5px;letter-spacing:.3px}
  .guarantee{position:absolute;left:285px;top:130px;height:43px;line-height:43px;color:var(--white);font-weight:800;font-size:27.5px;letter-spacing:.3px}
  .contact{position:absolute;display:flex;align-items:center;color:var(--white);white-space:nowrap}
  .contact__email{font-size:10.5px;letter-spacing:0;font-weight:400;line-height:15px}
  .contact__phone{font-size:28px;font-weight:400;letter-spacing:.5px;line-height:34px}
  .back-copy{position:absolute;right:25px;top:353px;text-align:right;color:var(--ink);font-size:13px;line-height:16px}
</style>
</head>
<body>

<section class="postcard postcard--front" aria-label="Postcard front">
  <svg class="postcard__art" viewBox="0 0 709 473">
    <defs>
      <linearGradient id="logsFill" x1="0" y1="0" x2="1" y2="1">
        <stop offset="0" stop-color="#a7653a"/>
        <stop offset=".35" stop-color="#5b8e3c"/>
        <stop offset=".65" stop-color="#c7d7cf"/>
        <stop offset="1" stop-color="#8f5a36"/>
      </linearGradient>
      <radialGradient id="stumpFill" cx=".5" cy=".45" r=".6">
        <stop offset="0" stop-color="#f3dc7d"/>
        <stop offset=".6" stop-color="#d9a237"/>
        <stop offset="1" stop-color="#6b4a28"/>
      </radialGradient>
      <path id="badgeArc" d="M441,325 A120,120 0 1,1 681,325 A120,120 0 1,1 441,325"/>
    </defs>
    <rect class="log-photo" x="0" y="208" width="470" height="265" fill="url(#logsFill)" role="img" aria-label="Photo of long stacked log piles along a grassy path beside a tree"/>
    <polygon class="panel-black" points="0,0 264,0 195,208 0,208" fill="var(--ink)"/>
    <polygon class="stripe-red" points="264,0 290,0 221,208 195,208" fill="var(--red)"/>
    <polygon class="band-sales" points="497,16 693,16 676,81 480,81" fill="var(--red)"/>
    <polygon class="band-channels" points="300,96 709,96 709,127 289,127" fill="var(--ink)"/>
    <polygon class="band-guarantee" points="268,130 709,130 709,173 255,173" fill="var(--red)"/>
    <circle cx="561" cy="325" r="152" fill="var(--white)"/>
    <rect x="0" y="412" width="709" height="5" fill="var(--red)"/>
    <polygon class="footer-stripe" points="138,417 160,417 140,473 118,473" fill="var(--red)"/>
    <polygon class="footer-band" points="150,417 709,417 709,473 130,473" fill="var(--ink)"/>
    <circle class="badge" cx="561" cy="325" r="138" fill="var(--ink)"/>
    <circle cx="561" cy="330" r="98" fill="url(#stumpFill)" role="img" aria-label="Illustration of a cartoon beaver lounging on a log over a tree stump"/>
    <text fill="var(--white)" font-family="Sora, sans-serif" font-weight="600" font-size="17.5" letter-spacing=".4">
      <textPath href="#badgeArc" startOffset="62">No order too big or too small</textPath>
    </text>
    <g class="icon-mail" transform="translate(162,437)">
      <rect width="20" height="15" fill="var(--red)"/>
      <polyline points="1,2 10,9 19,2" fill="none" stroke="var(--ink)" stroke-width="1.8"/>
    </g>
    <g class="icon-phone" transform="translate(444,433)">
      <rect width="22" height="22" fill="var(--red)"/>
      <path d="M7,5 l3,0 l1,4 l-2,1.5 q1.5,3 4,4 l1.5,-2 l4,1 l0,3 q-9,1 -11.5,-11.5z" fill="var(--amber)"/>
    </g>
  </svg>

  <div class="brand"><span class="brand__mark"></span><span class="brand__name">Wren Hollow<br>Farm</span></div>
  <h2 class="firm-title" style="top:96px">TREE FIRM</h2>
  <p class="firm-note front-note">Pick up or Delivery<br>Available</p>

  <h1 class="headline">SEASONED<br>FIREWOOD</h1>
  <div class="sales">SALES</div>
  <div class="channels">WHOLESALE ▪ RETAIL ▪ BULK</div>
  <div class="guarantee">BEST PRICED GUARANTEED</div>

  <div class="contact" style="left:190px;top:437px"><span class="contact__email">WRENHOLLOWFARM47@MAPLEPOST.NET</span></div>
  <div class="contact" style="left:477px;top:427px"><span class="contact__phone">615-302-4187</span></div>
</section>

<section class="postcard postcard--back" aria-label="Postcard back">
  <svg class="postcard__art" viewBox="0 0 709 473">
    <defs>
      <linearGradient id="splitFill" x1="0" y1="0" x2="0" y2="1">
        <stop offset="0" stop-color="#8a6a44"/>
        <stop offset=".5" stop-color="#c2834d"/>
        <stop offset="1" stop-color="#7d5434"/>
      </linearGradient>
      <linearGradient id="flameFill" x1="0" y1="0" x2="0" y2="1">
        <stop offset="0" stop-color="var(--yellow)"/>
        <stop offset="1" stop-color="var(--orange)"/>
      </linearGradient>
      <linearGradient id="sawFill" x1="0" y1="0" x2="1" y2="0">
        <stop offset="0" stop-color="#e4672a"/>
        <stop offset=".45" stop-color="#5a5a5a"/>
        <stop offset="1" stop-color="#d8d8d8"/>
      </linearGradient>
    </defs>
    <polygon class="flame-wedge" points="479,0 500,0 370,418 338,418" fill="url(#flameFill)"/>
    <polygon class="split-photo" points="292,0 479,0 405,238 300,300 200,310" fill="url(#splitFill)" role="img" aria-label="Photo of a pile of split firewood with cages of cut wood behind"/>
    <polygon class="orange-field" points="200,310 300,300 405,238 345,418 170,418" fill="url(#flameFill)"/>
    <polygon class="panel-black" points="0,0 264,0 110,473 0,473" fill="var(--ink)"/>
    <polygon class="stripe-red" points="264,0 292,0 200,310 170,418 138,473 110,473" fill="var(--red)"/>
    <rect class="chainsaw" x="24" y="256" width="350" height="175" rx="30" fill="url(#sawFill)" transform="rotate(-12 199 343)" role="img" aria-label="Photo of an orange chainsaw with a long guide bar"/>
    <rect class="stamp-box" x="606.5" y="33.5" width="78" height="77" rx="3" fill="none" stroke="var(--rule)" stroke-width="1"/>
    <line x1="461" y1="177" x2="684" y2="177" stroke="var(--rule)" stroke-width="1"/>
    <line x1="444" y1="242" x2="684" y2="242" stroke="var(--rule)" stroke-width="1"/>
    <line x1="417" y1="309" x2="684" y2="309" stroke="var(--rule)" stroke-width="1"/>
    <polygon class="footer-band" points="122,418 709,418 709,473 107,473" fill="var(--red)"/>
    <g class="icon-mail" transform="translate(128,438)">
      <rect width="23" height="16" fill="var(--white)"/>
      <polyline points="1,2 11.5,10 22,2" fill="none" stroke="var(--red)" stroke-width="1.8"/>
    </g>
    <g class="icon-phone" transform="translate(430,434)">
      <rect width="23" height="23" fill="var(--white)"/>
      <path d="M7,5 l3,0 l1,4 l-2,1.5 q1.5,3 4,4 l1.5,-2 l4,1 l0,3 q-9,1 -11.5,-11.5z" fill="var(--red)"/>
    </g>
  </svg>

  <div class="brand"><span class="brand__mark"></span><span class="brand__name">Wren Hollow<br>Farm</span></div>
  <h2 class="firm-title" style="top:104px;left:25px">TREE FIRM</h2>
  <p class="firm-note back-note">We sell firewood<br>in bulk bags</p>

  <p class="back-copy">We sell firewood from anything from<br>bagged wood to tractor trailer loads of wood</p>

  <div class="contact" style="left:160px;top:439px"><span class="contact__email">WRENHOLLOWFARM47@MAPLEPOST.NET</span></div>
  <div class="contact" style="left:466px;top:428px"><span class="contact__phone">615-302-4187</span></div>
</section>

</body>
</html>
```